A4 4-sided brochure - medical specialist

A4 sized, 4 sided brochure, glossy. I am a medical specialist (urologist) and need a brochure to hand out to GPs. I will write all text and will send photos. I have attached an example of the kind of thing I was thinking of. My website is https://www.harbourpointclinic.com.au/
There are three of us in a group but the brochure is just for me.
It is to give to GPs and not direct to patients, so should tell the GPs why they should refer to me.
Target Market(s)
Medical
Industry/Entity Type
medicine - surgery - urology
Requirements
Must have
- I have uploaded an outline of the layout with files that are listed on the outline - please load them up as indicated and submit your designs
Should not have
- Claims that I am the best

```html
<!DOCTYPE html>
<html lang="en">
<head>
<meta charset="utf-8">
<title>Owen Carrick Urologist – GP Brochure</title>
<link href="https://fonts.googleapis.com/css2?family=Montserrat:wght@400;500;600;700;800&display=swap" rel="stylesheet">
<style>
:root{
  --navy:#1c3e66;
  --navy-deep:#15314f;
  --cyan:#2bb5d6;
  --cyan-soft:#8fd6ea;
  --ink:#22384f;
  --muted:#5d6f82;
  --paper:#ffffff;
  --stage:#d8dbde;
}
*{box-sizing:border-box;margin:0;padding:0}
html,body{width:1200px;height:4000px;overflow:hidden}
body{background:var(--stage);font-family:'Montserrat',sans-serif;color:var(--ink);position:relative}
.spread{position:absolute;left:40px;width:1120px;height:792px;display:flex;box-shadow:0 12px 30px rgba(0,0,0,.18)}
.spread--outer{top:1100px}
.spread--inner{top:2100px}
.page{position:relative;width:560px;height:792px;background:var(--paper);overflow:hidden}
.page__bg{position:absolute;inset:0;width:560px;height:792px}
.abs{position:absolute}

.bullets{list-style:none}
.bullets li{position:relative;padding-left:11px;font-size:8px;line-height:1.3;margin-bottom:5px}
.bullets li::before{content:"";position:absolute;left:0;top:2px;width:5px;height:5px;border:1.2px solid var(--cyan);border-radius:50%}
.brand{display:flex;flex-direction:column;align-items:center;gap:6px}
.brand__dot{width:34px;height:34px;border-radius:50%;background:var(--cyan)}
.brand__name{font-size:21px;font-weight:500;color:var(--navy);letter-spacing:.2px}
.url{font-size:10px;font-weight:600;letter-spacing:2.4px;color:#fff;text-align:center}

.interest{top:34px;left:34px;width:460px;color:#fff}
.interest__banner{display:inline-block;background:var(--cyan);border-radius:3px;padding:4px 60px;font-size:15px;font-weight:800;color:#fff;margin-bottom:12px}
.interest__banner span{color:var(--navy)}
.interest__cols{display:flex;gap:20px}
.interest__cols ul{flex:1}
.interest .bullets li{color:#fff}
.back-brand{top:345px;left:0;width:560px}
.affiliations{top:560px;left:30px;width:130px;color:#fff}
.affiliations h3{font-size:12px;font-weight:700;color:var(--cyan);margin-bottom:10px}
.badge{height:18px;background:rgba(255,255,255,.85);border-radius:2px;margin-bottom:8px}
.badge--short{width:60%}
.badge--mid{width:80%}
.contact{top:560px;left:195px;width:330px;color:#fff}
.contact__name{font-size:18px;font-weight:700}
.contact__role{font-size:12px;color:var(--cyan);letter-spacing:9px;font-weight:500;margin:4px 0 10px}
.contact__line{display:flex;gap:7px;align-items:flex-start;font-size:8.5px;line-height:1.3;margin-bottom:5px}
.contact__line svg{flex:none;margin-top:1px}
.pill{display:inline-block;background:var(--cyan);color:var(--navy);font-size:8.5px;font-weight:700;padding:3px 10px;border-radius:3px;margin-top:4px}
.back-url{bottom:22px;left:0;width:560px}

.front-brand{top:40px;left:0;width:560px}
.portrait{top:150px;left:110px;width:340px;height:340px;border-radius:50%;background:radial-gradient(circle at 50% 40%,#c9d3dc 0%,#8c9fb2 45%,#3d5f86 100%);border:8px solid #fff;box-shadow:0 0 0 4px var(--cyan)}
.name-pill{top:468px;left:160px;width:240px;background:var(--cyan);border-radius:22px;text-align:center;padding:6px 0 5px}
.name-pill__name{font-size:20px;font-weight:600;color:var(--navy);line-height:1}
.name-pill__role{font-size:9px;font-weight:600;letter-spacing:8px;color:#fff;margin-top:3px}
.headline{top:560px;left:0;width:560px;text-align:center;color:#fff}
.headline__lead{font-size:18px;font-weight:700}
.headline__main{font-size:29px;font-weight:800;color:var(--cyan);line-height:1.05}
.headline__tail{font-size:13px;font-weight:600;margin-top:4px}
.front-url{top:680px;left:0;width:560px}

.about-strip{top:0;left:420px;width:100px;height:300px;background:var(--cyan);border-radius:0 0 30px 0}
.about-panel{top:0;left:0;width:470px;height:330px;background:var(--navy);border-radius:0 0 40px 0}
.about-head{top:38px;left:34px;font-size:20px;font-weight:700;color:#fff;line-height:1.05}
.about-head span{color:var(--cyan)}
.about-text{top:100px;left:34px;width:280px;color:#fff;font-size:7.6px;line-height:1.45;text-align:justify}
.about-text p{margin-bottom:10px}
.about-photo{top:55px;left:325px;width:140px;height:185px;background:linear-gradient(160deg,#d7dde3,#8193a6 70%,#3b516b);border:3px solid #fff}
.quals{top:360px;left:34px;width:220px}
.section-title{font-size:11px;font-weight:700;color:var(--navy);line-height:1.1;margin-bottom:10px}
.section-title span{color:var(--cyan)}
.quals .bullets li,.members .bullets li{color:var(--muted);font-size:7.6px}
.members{top:356px;left:275px;width:250px;border:2px solid var(--navy);padding:10px 12px 6px}
.members .bullets li{border-bottom:1px solid #d9e1e8;padding-bottom:4px}
.training{top:610px;left:34px;width:490px}
.training p{font-size:7.6px;line-height:1.45;color:var(--muted)}
.page-url{font-size:8px;color:var(--muted)}
.about-url{bottom:22px;left:34px}

.cancer-title{top:34px;left:34px;width:490px;font-size:12px;font-weight:700;color:var(--navy);line-height:1.2}
.cancer-cols{top:74px;left:34px;width:490px;display:flex;gap:16px}
.cancer-cols ul{flex:1}
.cancer-cols li{color:var(--muted);font-size:7.4px}
.gp-box{top:170px;left:34px;width:492px;height:240px;border:2px solid var(--navy);border-radius:10px}
.gp-tab{top:-2px;left:170px;width:150px;background:var(--navy);color:#fff;text-align:center;font-size:16px;font-weight:700;border-radius:0 0 6px 6px;padding:2px 0}
.gp-top{top:36px;left:12px;width:466px;display:flex;gap:10px}
.gp-top div{flex:1;font-size:8px;font-weight:700;color:var(--navy)}
.gp-top small{display:block;font-size:7.2px;font-weight:400;color:var(--muted);margin-top:2px}
.gp-help-title{top:68px;left:12px;font-size:9px;font-weight:700;color:var(--navy)}
.gp-help{top:84px;left:12px;width:466px;display:flex;gap:8px}
.gp-help ul{flex:1}
.gp-help li{font-size:7.2px;color:var(--muted);margin-bottom:3px}
.urgent{bottom:8px;left:18px;width:452px;background:var(--navy);border-radius:12px;color:#fff;font-size:9px;font-weight:600;display:flex;align-items:center;justify-content:center;gap:8px;padding:4px 0}
.urgent strong{font-size:12px;font-weight:700}
.conditions{top:425px;left:0;width:560px;height:367px;background:var(--navy);padding:20px 34px}
.conditions h2{font-size:20px;font-weight:700;color:#fff;margin-bottom:16px}
.conditions h2 span{color:var(--cyan)}
.cond-grid{display:grid;grid-template-columns:repeat(5,1fr);row-gap:18px;column-gap:10px}
.cond{color:#fff;font-size:7.6px;line-height:1.25}
.cond__icon{width:30px;height:30px;border-radius:50%;background:#fff;border:3px solid var(--cyan-soft);margin-bottom:5px;position:relative}
.cond__icon::after{content:"";position:absolute;inset:7px;border-radius:50%;border:2px solid var(--navy)}
.services-url{bottom:16px;right:34px;color:#c7d6e4}
</style>
</head>
<body>
<main class="brochure">

  <section class="spread spread--outer" aria-label="Outer spread">
    <article class="page page--back">
      <svg class="page__bg" viewBox="0 0 560 792" aria-hidden="true">
        <path d="M0 0H500Q560 0 560 60V110C560 250 430 330 290 330H0Z" fill="var(--navy)"/>
        <path d="M0 342H290C440 342 572 255 572 110" fill="none" stroke="var(--cyan)" stroke-width="5"/>
        <path d="M0 520Q290 585 560 455V792H0Z" fill="var(--navy)"/>
        <path d="M0 508Q290 573 560 443" fill="none" stroke="var(--cyan)" stroke-width="5"/>
      </svg>
      <div class="interest abs">
        <div class="interest__banner"><span>AREAS</span> OF INTEREST</div>
        <div class="interest__cols">
          <ul class="bullets">
            <li>PSA management</li>
            <li>BPH/LUTS medical and surgical treatment including laser, LiftRing and VaporCure</li>
            <li>UTI and haematuria assessment</li>
            <li>Kidney stone surgery and biochemical management</li>
            <li>Vasectomy and vasectomy reversal</li>
            <li>Robotic surgery, brachytherapy, and focal therapy for prostate cancer</li>
            <li>Robotic, open, and laparoscopic urology cancer surgery</li>
          </ul>
          <ul class="bullets">
            <li>Urodynamic investigation and female incontinence</li>
            <li>PTNS and Pharmaceutical neurotoxin management for overactive bladder</li>
            <li>Urinary tract infection management</li>
            <li>MRI-guided prostate biopsy</li>
            <li>Bladder cancer management</li>
            <li>Retroperitoneal lymph node dissection for testis cancer</li>
          </ul>
        </div>
      </div>
      <div class="brand back-brand abs">
        <div class="brand__dot"></div>
        <div class="brand__name">Harbour Point Clinic</div>
      </div>
      <div class="affiliations abs">
        <h3>AFFILIATIONS</h3>
        <div class="badge badge--mid"></div>
        <div class="badge"></div>
        <div class="badge badge--short"></div>
        <div class="badge badge--mid"></div>
        <div class="badge"></div>
        <div class="badge badge--short"></div>
      </div>
      <div class="contact abs">
        <div class="contact__name">A/PROF OWEN CARRICK</div>
        <div class="contact__role">UROLOGIST</div>
        <div class="contact__line"><svg width="10" height="10" viewBox="0 0 10 10"><path d="M2 1L4 3L3 4Q4 6 6 7L7 6L9 8L8 9Q3 9 1 2Z" fill="#fff"/></svg>0400 123 456 or 0400 987 654</div>
        <div class="contact__line"><svg width="10" height="10" viewBox="0 0 10 10"><rect x="1" y="2" width="8" height="7" rx="1" fill="#fff"/><rect x="3" y="1" width="4" height="2" fill="#fff"/></svg>08 7000 1234</div>
        <div class="contact__line"><svg width="10" height="10" viewBox="0 0 10 10"><rect x="1" y="2" width="8" height="6" fill="none" stroke="#fff"/><path d="M1 2L5 5L9 2" fill="none" stroke="#fff"/></svg>reception@owencarrick.org</div>
        <div class="contact__line"><svg width="10" height="10" viewBox="0 0 10 10"><path d="M5 10C2 6 1.5 4.5 1.5 3.5A3.5 3.5 0 0 1 8.5 3.5C8.5 4.5 8 6 5 10Z" fill="#fff"/></svg>Suite 4, Bayside North Private Hospital,<br>12 Wharf Street, Port Harbour SA 5000</div>
        <div class="pill">PO Box 100 Port Harbour SA 5000</div>
      </div>
      <div class="url back-url abs">www.harbourpointclinic.com.au</div>
    </article>

    <article class="page page--front">
      <svg class="page__bg" viewBox="0 0 560 792" aria-hidden="true">
        <path d="M0 400Q280 560 560 400V792H0Z" fill="var(--navy)"/>
        <path d="M0 388Q280 548 560 388" fill="none" stroke="var(--cyan)" stroke-width="6"/>
      </svg>
      <div class="brand front-brand abs">
        <div class="brand__dot"></div>
        <div class="brand__name">Harbour Point Clinic</div>
      </div>
      <div class="portrait abs" role="img" aria-label="Portrait of the urologist in surgical scrubs and cap in an operating theatre"></div>
      <div class="name-pill abs">
        <div class="name-pill__name">OWEN CARRICK</div>
        <div class="name-pill__role">UROLOGIST</div>
      </div>
      <div class="headline abs">
        <div class="headline__lead">I AM HERE TO SOLVE YOUR COMPLEX</div>
        <div class="headline__main">UROLOGICAL PROBLEM</div>
        <div class="headline__tail">WITH HIGH QUALITY CARE AND RAPID ACCESS</div>
      </div>
      <div class="url front-url abs">www.harbourpointclinic.com.au</div>
    </article>
  </section>

  <section class="spread spread--inner" aria-label="Inner spread">
    <article class="page page--about">
      <div class="about-strip abs"></div>
      <div class="about-panel abs"></div>
      <h1 class="about-head abs">ABOUT<br><span>OWEN CARRICK</span></h1>
      <div class="about-text abs">
        <p>A/Prof Owen Carrick is a consultant urologist with private practice at Bayside North Private and Westmere Hospitals. Owen consults at North Harbour, the Hills, and the South Coast, and undertakes Day Case lists at Glenelg and Seaford. He is Associate Professor at the University of Harbourside &amp; was senior staff specialist for 14 years at RHH.</p>
        <p>Owen undertook a urological cancer fellowship at the Kingsford General Hospital in Brisbane from 2008–2009, and was appointed as a consultant in Adelaide in 2009. He holds Fellowships of both the UK (FRCS Urol) and Australasian (FRACS Urol) Colleges of Surgeons, a Doctor of Medicine higher degree by research (MD) and has extensive basic science training (Bachelor of Science and Master of Science degrees).</p>
      </div>
      <div class="about-photo abs" role="img" aria-label="Head and shoulders portrait of the urologist in a suit"></div>
      <div class="quals abs">
        <h2 class="section-title">PROFESSIONAL<br><span>QUALIFICATIONS</span></h2>
        <ul class="bullets">
          <li>Bachelor of Science (1st Class Hons)<br>Westbridge University</li>
          <li>Master of Science, Southcourt University</li>
          <li>Bachelor of Medicine, Southcourt University</li>
          <li>Doctor of Medicine, Lestermoor University</li>
          <li>Fellow of the College of Surgical Fellows (Urology)</li>
          <li>Fellow of the Australasian Surgical College (Urology)</li>
        </ul>
      </div>
      <div class="members abs">
        <h2 class="section-title">PROFESSIONAL<br><span>MEMBERSHIPS</span></h2>
        <ul class="bullets">
          <li>FRCS(Urol)</li>
          <li>FRACS(Urol)</li>
          <li>Regional Urological Society</li>
          <li>Southern Prostate Cancer Trials Group</li>
          <li>Uro-Oncology Society</li>
          <li>Transpacific Urology Association</li>
          <li>Continental Urology Association</li>
        </ul>
      </div>
      <div class="training abs">
        <h2 class="section-title">TRAINING</h2>
        <p>Owen was the Urology Training Supervisor for urology surgery trainee doctors at the Royal Harbour Hospital. He was actively involved in the training and educational development of registrars and advanced trainees in simple and complex urological surgery and management.</p>
      </div>
      <div class="page-url about-url abs">www.harbourpointclinic.com.au</div>
    </article>

    <article class="page page--services">
      <h2 class="cancer-title abs">UROLOGICAL CANCER SERVICE DEVELOPMENT AT THE ROYAL HARBOUR HOSPITAL</h2>
      <div class="cancer-cols abs">
        <ul class="bullets">
          <li>Establishment of Prostate Cancer Specialist Nurse Service at RHH</li>
          <li>Chair PCSN rural roadshow education content committee</li>
          <li>Lead investigator for Cancer Registry CaP dataset collection</li>
        </ul>
        <ul class="bullets">
          <li>Multidisciplinary Urology Cancer Team</li>
          <li>Director of Urological Cancer</li>
          <li>Development of Joint Urological Oncology Clinics</li>
        </ul>
      </div>
      <div class="gp-box abs">
        <div class="gp-tab abs">FOR GPS</div>
        <div class="gp-top abs">
          <div>Make a Referral<small>GP Referral Form</small></div>
          <div>Urological Procedures<small>Urological Procedures</small></div>
          <div>Contact Harbour Point<small>Contact Harbour Point Urologist</small></div>
        </div>
        <div class="gp-help-title abs">Help with Urology Problems</div>
        <div class="gp-help abs">
          <ul class="bullets">
            <li>Epididymal Cysts</li><li>Epididymitis</li><li>Erectile Dysfunction</li><li>Haematospermia</li><li>Hydrocele</li><li>Incontinence in Women</li><li>Inflammation of the Foreskin / Balanitis</li><li>Microscopic Haematuria</li>
          </ul>
          <ul class="bullets">
            <li>Nocturnal Incontinence</li><li>Paraphimosis/Foreskin Stuck Behind Glans</li><li>Penile Curvature</li><li>Premature Ejaculation</li><li>Priapism</li><li>Retrograde Ejaculation</li><li>Screening for Prostate Cancer with PSA</li>
          </ul>
          <ul class="bullets">
            <li>Sterile Pyuria</li><li>Testosterone Deficiency / Hypogonadism</li><li>Tight Foreskin/Phimosis</li><li>Urethral Catheter Problems</li><li>Urinary Tract Infection in Men</li><li>Urinary Tract Infection in Women</li><li>Varicocoele (Adults)</li>
          </ul>
        </div>
        <div class="urgent abs">FOR URGENT REFERRALS CALL:
          <svg width="12" height="12" viewBox="0 0 10 10"><circle cx="5" cy="5" r="5" fill="#fff"/><path d="M3 2L4 3.5L3.5 4Q4 5.5 5.5 6.5L6 6L7.5 7L7 8Q3.5 7.5 2.5 3Z" fill="var(--navy)"/></svg>
          <strong>8000 4100</strong></div>
      </div>
      <section class="conditions abs">
        <h2>UROLOGY <span>CONDITIONS</span></h2>
        <div class="cond-grid">
          <div class="cond"><div class="cond__icon"></div>Blood in<br>the Urine</div>
          <div class="cond"><div class="cond__icon"></div>Epididymal<br>Cyst</div>
          <div class="cond"><div class="cond__icon"></div>Kidney Cysts<br>(Renal Cysts)</div>
          <div class="cond"><div class="cond__icon"></div>Kidney<br>Cancer</div>
          <div class="cond"><div class="cond__icon"></div>Prostate<br>Cancer</div>
          <div class="cond"><div class="cond__icon"></div>Impotence</div>
          <div class="cond"><div class="cond__icon"></div>Nocturia</div>
          <div class="cond"><div class="cond__icon"></div>Kidney Stones</div>
          <div class="cond"><div class="cond__icon"></div>Peyronie's<br>Disease</div>
          <div class="cond"><div class="cond__icon"></div>BPH – Benign<br>Prostatic<br>Hyperplasia</div>
          <div class="cond"><div class="cond__icon"></div>Premature<br>Ejaculation</div>
          <div class="cond"><div class="cond__icon"></div>Stage 1<br>Seminoma</div>
          <div class="cond"><div class="cond__icon"></div>Superficial<br>Bladder Cancer</div>
          <div class="cond"><div class="cond__icon"></div>Urinary<br>Incontinence in Men</div>
        </div>
      </section>
      <div class="page-url services-url abs">www.harbourpointclinic.com.au</div>
    </article>
  </section>

</main>
</body>
</html>
```